Social Media Cover and Profile

We already have our own logo. We just need a fresh design on our social media pages. We are not happy with our current designs. We would like to incorporate our ZING billboard and the colors are blue (#05143f) and white. You can also incorporate silver as well. We are a family law office (Divorce and Custody) We no longer want to incorporate the Capital of Harrisburg photo that we are currently using. You can look at our Social page; The Law Office of Milo T. Brennick.

Target Market(s)

Potential Clients

Industry/Entity Type

Family Law

Logo Text

Our Logo Is The Law Office of Milo T. Brennick with the Sheild

Requirements
Must have
• Text to include:
Central Pennslyvania's Premier Family Law Firm

Ability to be resized to and used as all images in social media, including but not limited to: Youtube Channel art, Social Cover and Profile.
Nice to have
• Darker color but we are open to "bright" ideas.

```html
<!DOCTYPE html>
<html lang="en">
<head>
<meta charset="utf-8">
<title>Milo T. Brennick – Social Cover Concepts</title>
<link rel="stylesheet" href="https://fonts.googleapis.com/css2?family=Cinzel:wght@400&family=Libre+Baskerville&family=Montserrat:wght@500;800&family=Roboto:wght@400;700&display=swap">
<style>
:root{
  --board:#1e1e1e;
  --navy:#05143f;
  --royal:#0b2b8c;
  --silver:#dfe3ea;
  --silver-dark:#9aa3b2;
  --white:#ffffff;
  --ink:#050505;
  --muted:#65676b;
  --chip:#e4e6eb;
  --blue:#1877f2;
  --red:#e41e3f;
  --dim:#3b3b3b;
}
*{margin:0;padding:0;box-sizing:border-box}
html,body{width:1200px;height:2548px;overflow:hidden;background:var(--board)}
.board{position:relative;width:1200px;height:2548px;font-family:"Roboto",Arial,sans-serif}

.firm{position:absolute;display:flex;align-items:center;gap:8px;font-family:"Montserrat",sans-serif;font-weight:500;color:var(--white);white-space:nowrap;line-height:1}
.firm-dot{display:block;border-radius:50%;border:2px solid currentColor}
.brand-mark{left:80px;top:96px;font-size:30px;gap:14px}
.brand-mark .firm-dot{width:56px;height:56px}
.cover .firm{font-size:15px}
.cover .firm .firm-dot{width:22px;height:22px}

.size-note{position:absolute;left:966px;top:130px;font-family:"Montserrat",sans-serif;font-weight:500;font-size:40px;color:var(--dim)}
.sample-label{position:absolute;left:61px;font-family:"Montserrat",sans-serif;font-weight:500;font-size:24px;color:var(--white);letter-spacing:.5px}

.mockup{position:absolute;left:61px;width:1077px;height:478px;background:var(--white);overflow:hidden;border:1px solid #cfd3da}
.topbar{position:absolute;left:0;top:0;width:100%;height:47px;background:var(--white);border-bottom:1px solid #dadde1}
.topbar .site-dot{position:absolute;left:14px;top:9px;width:30px;height:30px;border-radius:50%;background:var(--blue)}
.topbar .search{position:absolute;left:52px;top:9px;width:221px;height:30px;border-radius:15px;background:#f0f2f5;font-size:12px;color:var(--muted);line-height:30px;padding-left:27px}
.topbar .search svg{position:absolute;left:9px;top:9px}
.topbar .nav{position:absolute;top:13px}
.topbar .round{position:absolute;top:9px;width:30px;height:30px;border-radius:50%;background:var(--chip)}
.topbar .round svg{position:absolute;left:8px;top:8px}
.badge{position:absolute;width:14px;height:14px;border-radius:50%;background:var(--red);color:var(--white);font-size:9px;font-weight:700;text-align:center;line-height:14px}
.dot{position:absolute;width:7px;height:7px;border-radius:50%;background:var(--red)}
.scroll{position:absolute;right:0;top:47px;width:13px;height:431px;background:#f1f1f1}
.scroll::after{content:"";position:absolute;left:3px;top:18px;width:7px;height:70px;background:#c1c1c1;border-radius:2px}
.side-left{position:absolute;left:0;top:47px;width:160px;height:283px;background:linear-gradient(180deg,#9aa6bf 0%,#d8dde8 45%,#fff 75%)}
.side-right{position:absolute;left:906px;top:47px;width:158px;height:283px;background:linear-gradient(180deg,#7b6650 0%,#c7b9a8 45%,#fff 78%)}

.cover{position:absolute;left:160px;top:47px;width:746px;height:283px;background:linear-gradient(100deg,#0a1e5c 0%,var(--royal) 60%,#0d2f95 100%);overflow:hidden;color:var(--white)}
.cover .photo{position:absolute;left:0;top:0;width:62%;height:100%;background:linear-gradient(90deg,rgba(5,20,63,.75) 0%,rgba(30,60,110,.55) 45%,rgba(11,43,140,0) 100%)}
.zing{position:absolute;font-family:"Cinzel",serif;font-weight:400;font-size:104px;line-height:1;letter-spacing:4px;background:linear-gradient(180deg,#ffffff 0%,var(--silver) 45%,var(--silver-dark) 70%,#f4f6f9 100%);-webkit-background-clip:text;background-clip:text;color:transparent}
.divider{position:absolute;width:2px;background:rgba(255,255,255,.55)}
.headline{position:absolute;font-family:"Cinzel",serif;font-weight:400;font-size:36px;line-height:38px;color:var(--white);white-space:nowrap}
.headline.bold{font-family:"Montserrat",sans-serif;font-weight:800;font-size:33px;line-height:36px;text-align:center;width:746px;left:0}
.url{position:absolute;font-family:"Libre Baskerville",serif;font-size:15px;letter-spacing:1.6px;color:var(--white);white-space:nowrap}
.url.sans{font-family:"Roboto",sans-serif;letter-spacing:.6px}

.avatar{position:absolute;left:189px;top:312px;width:106px;height:106px;border-radius:50%;background:var(--white);border:1px solid #dadde1}
.avatar span{position:absolute;left:0;top:47px;width:100%;text-align:center;font-family:"Montserrat",sans-serif;font-weight:500;font-size:9px;color:var(--navy)}
.page-name{position:absolute;left:316px;top:345px;font-size:22px;font-weight:700;line-height:26px;color:var(--ink);width:300px}
.page-cat{position:absolute;left:316px;top:400px;font-size:13px;color:var(--muted)}
.call-btn{position:absolute;left:632px;top:381px;width:246px;height:31px;border-radius:5px;background:var(--blue);color:var(--white);font-size:13px;font-weight:700;text-align:center;line-height:31px}
.call-btn svg{vertical-align:-2px;margin-right:4px}
.rule{position:absolute;left:187px;top:432px;width:691px;height:1px;background:#dadde1}
.tabs{position:absolute;left:200px;top:451px;font-size:12px;color:var(--muted);display:flex;gap:26px}
.tabs .active{color:var(--blue)}
.act{position:absolute;top:444px;height:28px;border-radius:5px;background:var(--chip);font-size:12px;color:var(--ink);display:flex;align-items:center;justify-content:center;gap:5px}
</style>
</head>
<body>
<main class="board">
  <div class="firm brand-mark"><span class="firm-dot"></span>Milo T. Brennick</div>
  <div class="size-note">851X310</div>

  <!-- Sample 1 -->
  <section class="mockup" style="top:203px">
    <div class="topbar">
      <div class="site-dot"></div>
      <div class="search"><svg width="12" height="12" viewBox="0 0 12 12"><circle cx="5" cy="5" r="4" fill="none" stroke="#65676b" stroke-width="1.5"/><line x1="8" y1="8" x2="11" y2="11" stroke="#65676b" stroke-width="1.5"/></svg>Search Social</div>
      <svg class="nav" style="left:335px" width="20" height="20" viewBox="0 0 20 20"><path d="M3 9 L10 3 L17 9 V17 H3 Z" fill="none" stroke="#65676b" stroke-width="1.6"/></svg>
      <svg class="nav" style="left:430px" width="20" height="20" viewBox="0 0 20 20"><rect x="2" y="4" width="16" height="12" rx="2" fill="none" stroke="#65676b" stroke-width="1.6"/><path d="M8 7 L13 10 L8 13 Z" fill="#65676b"/></svg>
      <div class="badge" style="left:445px;top:6px">9</div>
      <svg class="nav" style="left:524px" width="20" height="20" viewBox="0 0 20 20"><path d="M3 4 H17 V8 H3 Z M4 8 V17 H16 V8" fill="none" stroke="#65676b" stroke-width="1.6"/></svg>
      <svg class="nav" style="left:618px" width="20" height="20" viewBox="0 0 20 20"><circle cx="10" cy="10" r="8" fill="none" stroke="#65676b" stroke-width="1.6"/><circle cx="10" cy="8" r="2" fill="#65676b"/></svg>
      <svg class="nav" style="left:712px" width="20" height="20" viewBox="0 0 20 20"><rect x="3" y="3" width="14" height="14" fill="none" stroke="#65676b" stroke-width="1.6"/><path d="M7 7 H17 M7 7 V17" stroke="#65676b" stroke-width="1.6"/></svg>
      <div class="round" style="left:905px"><svg width="14" height="14" viewBox="0 0 14 14"><path d="M7 1 V13 M1 7 H13" stroke="#050505" stroke-width="1.8"/></svg></div>
      <div class="round" style="left:943px"><svg width="14" height="14" viewBox="0 0 14 14"><circle cx="7" cy="7" r="6" fill="#050505"/></svg></div>
      <div class="round" style="left:981px"><svg width="14" height="14" viewBox="0 0 14 14"><path d="M3 10 V6 A4 4 0 0 1 11 6 V10 Z M6 11 H8" fill="#050505" stroke="#050505"/></svg></div>
      <div class="badge" style="left:1006px;top:3px">5</div>
      <div class="round" style="left:1019px"><svg width="14" height="14" viewBox="0 0 14 14"><path d="M3 5 L7 10 L11 5 Z" fill="#050505"/></svg></div>
      <div class="dot" style="left:1044px;top:8px"></div>
    </div>
    <div class="side-left"></div><div class="side-right"></div><div class="scroll"></div>
    <div class="cover">
      <div class="photo" role="img" aria-label="Capitol dome photograph in deep blue tones"></div>
      <div class="zing" style="left:32px;top:80px">ZING</div>
      <div class="divider" style="left:378px;top:48px;height:152px"></div>
      <div class="headline" style="left:424px;top:46px">Central<br>Pennslyvania's<br>Premier Family<br>Law Firm</div>
      <div class="url" style="left:424px;top:238px">www.milobrennicklaw.com</div>
      <div class="firm" style="left:40px;top:231px"><span class="firm-dot"></span>Milo T. Brennick</div>
    </div>
    <div class="avatar"><span>Milo T. Brennick</span></div>
    <div class="page-name">The Law Office of Milo T. Brennick</div>
    <div class="page-cat">Divorce &amp; Family Lawyer</div>
    <div class="call-btn"><svg width="12" height="12" viewBox="0 0 12 12"><path d="M2 1 L4.5 1 L5.5 4 L4 5 Q5 7.5 7 8 L8 6.5 L11 7.5 V10 Q11 11 10 11 Q1 10 1 2 Q1 1 2 1 Z" fill="#fff"/></svg>Call Now</div>
    <div class="rule"></div>
    <div class="tabs"><span class="active">Home</span><span>Photos</span><span>Videos</span><span>About</span><span>More ▾</span></div>
    <div class="act" style="left:617px;width:86px"><svg width="12" height="12" viewBox="0 0 12 12"><path d="M1 5 H3 V11 H1 Z M4 5 L6 1 Q7.5 1 7 4 H10.5 Q11.5 4.5 11 6 L10 10.5 Q9.8 11 9 11 H4 Z" fill="#050505"/></svg>Like</div>
    <div class="act" style="left:709px;width:85px"><svg width="12" height="12" viewBox="0 0 12 12"><circle cx="6" cy="6" r="5.5" fill="#050505"/></svg>Message</div>
    <div class="act" style="left:799px;width:37px"><svg width="12" height="12" viewBox="0 0 12 12"><circle cx="5" cy="5" r="4" fill="none" stroke="#050505" stroke-width="1.5"/><line x1="8" y1="8" x2="11" y2="11" stroke="#050505" stroke-width="1.5"/></svg></div>
    <div class="act" style="left:842px;width:36px">···</div>
  </section>
  <div class="sample-label" style="top:696px">SAMPLE 1</div>

  <!-- Sample 2 -->
  <section class="mockup" style="top:774px">
    <div class="topbar">
      <div class="site-dot"></div>
      <div class="search"><svg width="12" height="12" viewBox="0 0 12 12"><circle cx="5" cy="5" r="4" fill="none" stroke="#65676b" stroke-width="1.5"/><line x1="8" y1="8" x2="11" y2="11" stroke="#65676b" stroke-width="1.5"/></svg>Search Social</div>
      <svg class="nav" style="left:335px" width="20" height="20" viewBox="0 0 20 20"><path d="M3 9 L10 3 L17 9 V17 H3 Z" fill="none" stroke="#65676b" stroke-width="1.6"/></svg>
      <svg class="nav" style="left:430px" width="20" height="20" viewBox="0 0 20 20"><rect x="2" y="4" width="16" height="12" rx="2" fill="none" stroke="#65676b" stroke-width="1.6"/><path d="M8 7 L13 10 L8 13 Z" fill="#65676b"/></svg>
      <div class="badge" style="left:445px;top:6px">9</div>
      <svg class="nav" style="left:524px" width="20" height="20" viewBox="0 0 20 20"><path d="M3 4 H17 V8 H3 Z M4 8 V17 H16 V8" fill="none" stroke="#65676b" stroke-width="1.6"/></svg>
      <svg class="nav" style="left:618px" width="20" height="20" viewBox="0 0 20 20"><circle cx="10" cy="10" r="8" fill="none" stroke="#65676b" stroke-width="1.6"/><circle cx="10" cy="8" r="2" fill="#65676b"/></svg>
      <svg class="nav" style="left:712px" width="20" height="20" viewBox="0 0 20 20"><rect x="3" y="3" width="14" height="14" fill="none" stroke="#65676b" stroke-width="1.6"/><path d="M7 7 H17 M7 7 V17" stroke="#65676b" stroke-width="1.6"/></svg>
      <div class="round" style="left:905px"><svg width="14" height="14" viewBox="0 0 14 14"><path d="M7 1 V13 M1 7 H13" stroke="#050505" stroke-width="1.8"/></svg></div>
      <div class="round" style="left:943px"><svg width="14" height="14" viewBox="0 0 14 14"><circle cx="7" cy="7" r="6" fill="#050505"/></svg></div>
      <div class="round" style="left:981px"><svg width="14" height="14" viewBox="0 0 14 14"><path d="M3 10 V6 A4 4 0 0 1 11 6 V10 Z M6 11 H8" fill="#050505" stroke="#050505"/></svg></div>
      <div class="badge" style="left:1006px;top:3px">5</div>
      <div class="round" style="left:1019px"><svg width="14" height="14" viewBox="0 0 14 14"><path d="M3 5 L7 10 L11 5 Z" fill="#050505"/></svg></div>
      <div class="dot" style="left:1044px;top:8px"></div>
    </div>
    <div class="side-left"></div><div class="side-right"></div><div class="scroll"></div>
    <div class="cover">
      <div class="photo" role="img" aria-label="Capitol dome photograph in deep blue tones"></div>
      <div class="firm" style="left:40px;top:32px"><span class="firm-dot"></span>Milo T. Brennick</div>
      <div class="zing" style="left:32px;top:102px">ZING</div>
      <div class="divider" style="left:384px;top:76px;height:150px"></div>
      <div class="headline" style="left:436px;top:76px">Central<br>Pennslyvania's<br>Premier Family<br>Law Firm</div>
      <div class="url" style="left:258px;top:249px">www.milobrennicklaw.com</div>
    </div>
    <div class="avatar"><span>Milo T. Brennick</span></div>
    <div class="page-name">The Law Office of Milo T. Brennick</div>
    <div class="page-cat">Divorce &amp; Family Lawyer</div>
    <div class="call-btn"><svg width="12" height="12" viewBox="0 0 12 12"><path d="M2 1 L4.5 1 L5.5 4 L4 5 Q5 7.5 7 8 L8 6.5 L11 7.5 V10 Q11 11 10 11 Q1 10 1 2 Q1 1 2 1 Z" fill="#fff"/></svg>Call Now</div>
    <div class="rule"></div>
    <div class="tabs"><span class="active">Home</span><span>Photos</span><span>Videos</span><span>About</span><span>More ▾</span></div>
    <div class="act" style="left:617px;width:86px"><svg width="12" height="12" viewBox="0 0 12 12"><path d="M1 5 H3 V11 H1 Z M4 5 L6 1 Q7.5 1 7 4 H10.5 Q11.5 4.5 11 6 L10 10.5 Q9.8 11 9 11 H4 Z" fill="#050505"/></svg>Like</div>
    <div class="act" style="left:709px;width:85px"><svg width="12" height="12" viewBox="0 0 12 12"><circle cx="6" cy="6" r="5.5" fill="#050505"/></svg>Message</div>
    <div class="act" style="left:799px;width:37px"><svg width="12" height="12" viewBox="0 0 12 12"><circle cx="5" cy="5" r="4" fill="none" stroke="#050505" stroke-width="1.5"/><line x1="8" y1="8" x2="11" y2="11" stroke="#050505" stroke-width="1.5"/></svg></div>
    <div class="act" style="left:842px;width:36px">···</div>
  </section>
  <div class="sample-label" style="top:1266px">SAMPLE 2</div>

  <!-- Sample 3 -->
  <section class="mockup" style="top:1350px">
    <div class="topbar">
      <div class="site-dot"></div>
      <div class="search"><svg width="12" height="12" viewBox="0 0 12 12"><circle cx="5" cy="5" r="4" fill="none" stroke="#65676b" stroke-width="1.5"/><line x1="8" y1="8" x2="11" y2="11" stroke="#65676b" stroke-width="1.5"/></svg>Search Social</div>
      <svg class="nav" style="left:335px" width="20" height="20" viewBox="0 0 20 20"><path d="M3 9 L10 3 L17 9 V17 H3 Z" fill="none" stroke="#65676b" stroke-width="1.6"/></svg>
      <svg class="nav" style="left:430px" width="20" height="20" viewBox="0 0 20 20"><rect x="2" y="4" width="16" height="12" rx="2" fill="none" stroke="#65676b" stroke-width="1.6"/><path d="M8 7 L13 10 L8 13 Z" fill="#65676b"/></svg>
      <div class="badge" style="left:445px;top:6px">9</div>
      <svg class="nav" style="left:524px" width="20" height="20" viewBox="0 0 20 20"><path d="M3 4 H17 V8 H3 Z M4 8 V17 H16 V8" fill="none" stroke="#65676b" stroke-width="1.6"/></svg>
      <svg class="nav" style="left:618px" width="20" height="20" viewBox="0 0 20 20"><circle cx="10" cy="10" r="8" fill="none" stroke="#65676b" stroke-width="1.6"/><circle cx="10" cy="8" r="2" fill="#65676b"/></svg>
      <svg class="nav" style="left:712px" width="20" height="20" viewBox="0 0 20 20"><rect x="3" y="3" width="14" height="14" fill="none" stroke="#65676b" stroke-width="1.6"/><path d="M7 7 H17 M7 7 V17" stroke="#65676b" stroke-width="1.6"/></svg>
      <div class="round" style="left:905px"><svg width="14" height="14" viewBox="0 0 14 14"><path d="M7 1 V13 M1 7 H13" stroke="#050505" stroke-width="1.8"/></svg></div>
      <div class="round" style="left:943px"><svg width="14" height="14" viewBox="0 0 14 14"><circle cx="7" cy="7" r="6" fill="#050505"/></svg></div>
      <div class="round" style="left:981px"><svg width="14" height="14" viewBox="0 0 14 14"><path d="M3 10 V6 A4 4 0 0 1 11 6 V10 Z M6 11 H8" fill="#050505" stroke="#050505"/></svg></div>
      <div class="badge" style="left:1006px;top:3px">5</div>
      <div class="round" style="left:1019px"><svg width="14" height="14" viewBox="0 0 14 14"><path d="M3 5 L7 10 L11 5 Z" fill="#050505"/></svg></div>
      <div class="dot" style="left:1044px;top:8px"></div>
    </div>
    <div class="side-left"></div><div class="side-right"></div><div class="scroll"></div>
    <div class="cover">
      <div class="photo" role="img" aria-label="Capitol dome photograph in deep blue tones"></div>
      <div class="firm" style="left:282px;top:36px"><span class="firm-dot"></span>Milo T. Brennick</div>
      <div class="zing" style="left:36px;top:108px">ZING</div>
      <div class="divider" style="left:384px;top:90px;height:135px"></div>
      <div class="headline" style="left:438px;top:84px">Central<br>Pennslyvania's<br>Premier Family<br>Law Firm</div>
      <div class="url" style="left:258px;top:250px">www.milobrennicklaw.com</div>
    </div>
    <div class="avatar"><span>Milo T. Brennick</span></div>
    <div class="page-name">The Law Office of Milo T. Brennick</div>
    <div class="page-cat">Divorce &amp; Family Lawyer</div>
    <div class="call-btn"><svg width="12" height="12" viewBox="0 0 12 12"><path d="M2 1 L4.5 1 L5.5 4 L4 5 Q5 7.5 7 8 L8 6.5 L11 7.5 V10 Q11 11 10 11 Q1 10 1 2 Q1 1 2 1 Z" fill="#fff"/></svg>Call Now</div>
    <div class="rule"></div>
    <div class="tabs"><span class="active">Home</span><span>Photos</span><span>Videos</span><span>About</span><span>More ▾</span></div>
    <div class="act" style="left:617px;width:86px"><svg width="12" height="12" viewBox="0 0 12 12"><path d="M1 5 H3 V11 H1 Z M4 5 L6 1 Q7.5 1 7 4 H10.5 Q11.5 4.5 11 6 L10 10.5 Q9.8 11 9 11 H4 Z" fill="#050505"/></svg>Like</div>
    <div class="act" style="left:709px;width:85px"><svg width="12" height="12" viewBox="0 0 12 12"><circle cx="6" cy="6" r="5.5" fill="#050505"/></svg>Message</div>
    <div class="act" style="left:799px;width:37px"><svg width="12" height="12" viewBox="0 0 12 12"><circle cx="5" cy="5" r="4" fill="none" stroke="#050505" stroke-width="1.5"/><line x1="8" y1="8" x2="11" y2="11" stroke="#050505" stroke-width="1.5"/></svg></div>
    <div class="act" style="left:842px;width:36px">···</div>
  </section>
  <div class="sample-label" style="top:1847px">SAMPLE 3</div>

  <!-- Sample 4 -->
  <section class="mockup" style="top:1932px">
    <div class="topbar">
      <div class="site-dot"></div>
      <div class="search"><svg width="12" height="12" viewBox="0 0 12 12"><circle cx="5" cy="5" r="4" fill="none" stroke="#65676b" stroke-width="1.5"/><line x1="8" y1="8" x2="11" y2="11" stroke="#65676b" stroke-width="1.5"/></svg>Search Social</div>
      <svg class="nav" style="left:335px" width="20" height="20" viewBox="0 0 20 20"><path d="M3 9 L10 3 L17 9 V17 H3 Z" fill="none" stroke="#65676b" stroke-width="1.6"/></svg>
      <svg class="nav" style="left:430px" width="20" height="20" viewBox="0 0 20 20"><rect x="2" y="4" width="16" height="12" rx="2" fill="none" stroke="#65676b" stroke-width="1.6"/><path d="M8 7 L13 10 L8 13 Z" fill="#65676b"/></svg>
      <div class="badge" style="left:445px;top:6px">9</div>
      <svg class="nav" style="left:524px" width="20" height="20" viewBox="0 0 20 20"><path d="M3 4 H17 V8 H3 Z M4 8 V17 H16 V8" fill="none" stroke="#65676b" stroke-width="1.6"/></svg>
      <svg class="nav" style="left:618px" width="20" height="20" viewBox="0 0 20 20"><circle cx="10" cy="10" r="8" fill="none" stroke="#65676b" stroke-width="1.6"/><circle cx="10" cy="8" r="2" fill="#65676b"/></svg>
      <svg class="nav" style="left:712px" width="20" height="20" viewBox="0 0 20 20"><rect x="3" y="3" width="14" height="14" fill="none" stroke="#65676b" stroke-width="1.6"/><path d="M7 7 H17 M7 7 V17" stroke="#65676b" stroke-width="1.6"/></svg>
      <div class="round" style="left:905px"><svg width="14" height="14" viewBox="0 0 14 14"><path d="M7 1 V13 M1 7 H13" stroke="#050505" stroke-width="1.8"/></svg></div>
      <div class="round" style="left:943px"><svg width="14" height="14" viewBox="0 0 14 14"><circle cx="7" cy="7" r="6" fill="#050505"/></svg></div>
      <div class="round" style="left:981px"><svg width="14" height="14" viewBox="0 0 14 14"><path d="M3 10 V6 A4 4 0 0 1 11 6 V10 Z M6 11 H8" fill="#050505" stroke="#050505"/></svg></div>
      <div class="badge" style="left:1006px;top:3px">5</div>
      <div class="round" style="left:1019px"><svg width="14" height="14" viewBox="0 0 14 14"><path d="M3 5 L7 10 L11 5 Z" fill="#050505"/></svg></div>
      <div class="dot" style="left:1044px;top:8px"></div>
    </div>
    <div class="side-left"></div><div class="side-right"></div><div class="scroll"></div>
    <div class="cover">
      <div class="photo" role="img" aria-label="Capitol dome photograph in deep blue tones"></div>
      <div class="zing" style="left:0;width:746px;text-align:center;top:22px;font-size:96px">ZING</div>
      <div class="headline bold" style="top:138px">CENTRAL PENNSLYVANIA'S PREMIER<br>FAMILY LAW FIRM</div>
      <div class="firm" style="left:40px;top:233px"><span class="firm-dot"></span>Milo T. Brennick</div>
      <div class="url sans" style="left:496px;top:241px">www.milobrennicklaw.com</div>
    </div>
    <div class="avatar"><span>Milo T. Brennick</span></div>
    <div class="page-name">The Law Office of Milo T. Brennick</div>
    <div class="page-cat">Divorce &amp; Family Lawyer</div>
    <div class="call-btn"><svg width="12" height="12" viewBox="0 0 12 12"><path d="M2 1 L4.5 1 L5.5 4 L4 5 Q5 7.5 7 8 L8 6.5 L11 7.5 V10 Q11 11 10 11 Q1 10 1 2 Q1 1 2 1 Z" fill="#fff"/></svg>Call Now</div>
    <div class="rule"></div>
    <div class="tabs"><span class="active">Home</span><span>Photos</span><span>Videos</span><span>About</span><span>More ▾</span></div>
    <div class="act" style="left:617px;width:86px"><svg width="12" height="12" viewBox="0 0 12 12"><path d="M1 5 H3 V11 H1 Z M4 5 L6 1 Q7.5 1 7 4 H10.5 Q11.5 4.5 11 6 L10 10.5 Q9.8 11 9 11 H4 Z" fill="#050505"/></svg>Like</div>
    <div class="act" style="left:709px;width:85px"><svg width="12" height="12" viewBox="0 0 12 12"><circle cx="6" cy="6" r="5.5" fill="#050505"/></svg>Message</div>
    <div class="act" style="left:799px;width:37px"><svg width="12" height="12" viewBox="0 0 12 12"><circle cx="5" cy="5" r="4" fill="none" stroke="#050505" stroke-width="1.5"/><line x1="8" y1="8" x2="11" y2="11" stroke="#050505" stroke-width="1.5"/></svg></div>
    <div class="act" style="left:842px;width:36px">···</div>
  </section>
  <div class="sample-label" style="top:2429px">SAMPLE 4</div>
</main>
</body>
</html>
```